Stationery Design Project

Please create a custom Stationery Design for Pinecrest Dwellings. The logo is attached to this brief.

Please Include:
- Letterhead
- With Compliments slip
- Envelope

Please also see open Business Card project: http://briefs.sketchvault.example/task.aspx?id=517290

Industry/Entity Type

Business

```html
<!DOCTYPE html>
<html lang="en">
<head>
<meta charset="utf-8">
<title>Pinecrest Dwellings – Stationery</title>
<link rel="stylesheet" href="https://fonts.googleapis.com/css2?family=Source+Sans+3:wght@400;600&display=swap">
<style>
  :root {
    --stage: #5e5e5e;
    --paper: #ffffff;
    --brand-blue: #0a6cb8;
    --brand-green: #8cc63f;
    --brand-yellow: #f6c915;
    --mark-grey: #e2e2e2;
    --ink: #555555;
    --rule: #b5b5b5;
    --flap-line: #b9b9b9;
  }
  * { box-sizing: border-box; margin: 0; padding: 0; }
  html, body { width: 1200px; height: 640px; overflow: hidden; }
  body {
    background: var(--stage);
    font-family: "Source Sans 3", Arial, sans-serif;
    position: relative;
  }
  .sheet {
    position: absolute;
    background: var(--paper);
    overflow: hidden;
  }
  .letterhead { left: 72px; top: 56px; width: 392px; height: 536px; }
  .envelope-front { left: 551px; top: 22px; width: 429px; height: 191px; }
  .envelope-back { left: 724px; top: 230px; width: 446px; height: 179px; }
  .comp-slip { left: 578px; top: 438px; width: 347px; height: 154px; }

  .brand-lockup {
    position: absolute;
    display: flex;
    flex-direction: column;
    align-items: center;
    gap: 4px;
  }
  .brand-dot {
    width: 18px; height: 18px; border-radius: 50%;
    background: var(--brand-yellow);
  }
  .brand-name {
    color: var(--brand-blue);
    font-weight: 600;
    font-size: 15px;
    line-height: 1.05;
    text-align: center;
  }
  .letterhead .brand-lockup { left: 50%; top: 26px; transform: translateX(-50%); }
  .letterhead .brand-dot { width: 24px; height: 24px; }
  .letterhead .brand-name { font-size: 18px; }

  .envelope-front .brand-lockup { left: 26px; top: 118px; }
  .envelope-front .brand-name { font-size: 13px; }
  .envelope-back .brand-lockup { left: 50%; top: 12px; transform: translateX(-50%); }
  .envelope-back .brand-dot { width: 16px; height: 16px; }
  .envelope-back .brand-name { font-size: 10px; }
  .comp-slip .brand-lockup { left: 22px; top: 96px; }
  .comp-slip .brand-name { font-size: 12px; }

  .brand-mark-faint {
    position: absolute;
    border-radius: 50%;
    background: var(--mark-grey);
  }
  .letterhead .brand-mark-faint { width: 140px; height: 140px; right: 14px; bottom: 44px; }
  .envelope-front .brand-mark-faint { width: 96px; height: 96px; right: 18px; bottom: 26px; }
  .comp-slip .brand-mark-faint { width: 74px; height: 74px; right: 24px; bottom: 26px; }

  .contact {
    position: absolute;
    display: flex;
    align-items: center;
    gap: 6px;
    font-size: 5.5px;
    color: var(--ink);
    line-height: 1.5;
  }
  .contact .address { padding-right: 6px; border-right: 1px solid var(--rule); }
  .letterhead .contact { left: 32px; bottom: 34px; }
  .letterhead .contact .address { text-align: right; }
  .envelope-front .contact { left: 124px; top: 150px; font-size: 5px; }
  .comp-slip .contact { left: 98px; top: 210px; top: 124px; font-size: 4.6px; }
  .contact-lines { display: flex; flex-direction: column; }
  .contact-line { display: flex; align-items: center; gap: 3px; }
  .contact-icon { width: 6px; height: 6px; display: block; }

  .slip-title {
    position: absolute;
    right: 26px; top: 22px;
    color: var(--brand-blue);
    font-size: 13px;
    font-weight: 400;
  }

  .accent-band {
    position: absolute;
    left: 0; bottom: 0;
    width: 100%;
    display: block;
  }
  .letterhead .accent-band { height: 24px; }
  .envelope-front .accent-band { height: 18px; }
  .comp-slip .accent-band { height: 16px; }
  .band-green { fill: var(--brand-green); }
  .band-blue { fill: var(--brand-blue); }

  .flap { position: absolute; left: 0; top: 0; width: 100%; height: 50px; display: block; }
  .flap-edge { fill: none; stroke: var(--flap-line); stroke-width: 1; }
</style>
</head>
<body>

<svg width="0" height="0" style="position:absolute">
  <defs>
    <symbol id="icon-phone" viewBox="0 0 10 10">
      <rect width="10" height="10" rx="1.5" fill="#0a6cb8"/>
      <path d="M3 2.5 L4.2 2.5 L4.6 4 L3.9 4.6 Q4.6 5.9 5.6 6.3 L6.1 5.6 L7.5 6 L7.5 7.2 Q4 7.5 3 2.5Z" fill="#fff"/>
    </symbol>
    <symbol id="icon-web" viewBox="0 0 10 10">
      <rect width="10" height="10" rx="1.5" fill="#0a6cb8"/>
      <circle cx="5" cy="5" r="2.8" fill="none" stroke="#fff" stroke-width="0.8"/>
      <path d="M2.2 5 H7.8 M5 2.2 V7.8" stroke="#fff" stroke-width="0.6"/>
    </symbol>
    <symbol id="band" viewBox="0 0 400 24" preserveAspectRatio="none">
      <path class="band-green" d="M0 7 L250 7 Q290 8 318 24 L0 24 Z"/>
      <path class="band-blue" d="M318 12 L400 12 L400 24 L338 24 Q330 16 318 12 Z"/>
    </symbol>
  </defs>
</svg>

<section class="sheet letterhead" aria-label="Letterhead">
  <div class="brand-lockup">
    <span class="brand-dot"></span>
    <span class="brand-name">Pinecrest Dwellings</span>
  </div>
  <div class="brand-mark-faint" role="img" aria-label="Faint brand symbol"></div>
  <div class="contact">
    <div class="address">12 Alder Court<br>Westbrook Business Park, City Name</div>
    <div class="contact-lines">
      <span class="contact-line"><svg class="contact-icon"><use href="#icon-phone"/></svg>020 7946 0321</span>
      <span class="contact-line"><svg class="contact-icon"><use href="#icon-web"/></svg>www.pinecrestdwellings.example</span>
    </div>
  </div>
  <svg class="accent-band" preserveAspectRatio="none" viewBox="0 0 400 24"><use href="#band"/></svg>
</section>

<section class="sheet envelope-front" aria-label="Envelope front">
  <div class="brand-lockup">
    <span class="brand-dot"></span>
    <span class="brand-name">Pinecrest<br>Dwellings</span>
  </div>
  <div class="brand-mark-faint" role="img" aria-label="Faint brand symbol"></div>
  <div class="contact">
    <div class="address" style="text-align:left">12 Alder Court, Address Line<br>Westbrook Business Park, City Name</div>
  </div>
  <svg class="accent-band" preserveAspectRatio="none" viewBox="0 0 400 24"><use href="#band"/></svg>
</section>

<section class="sheet envelope-back" aria-label="Envelope back">
  <svg class="flap" viewBox="0 0 446 50" preserveAspectRatio="none">
    <path class="flap-edge" d="M0 1 Q0 48 28 48 L418 48 Q446 48 446 1"/>
  </svg>
  <div class="brand-lockup">
    <span class="brand-dot"></span>
    <span class="brand-name">Pinecrest Dwellings</span>
  </div>
</section>

<section class="sheet comp-slip" aria-label="With compliments slip">
  <h2 class="slip-title">With Compliments</h2>
  <div class="brand-lockup">
    <span class="brand-dot"></span>
    <span class="brand-name">Pinecrest<br>Dwellings</span>
  </div>
  <div class="brand-mark-faint" role="img" aria-label="Faint brand symbol"></div>
  <div class="contact">
    <div class="address" style="text-align:left">12 Alder Court, Address Line<br>Westbrook Business Park, City Name</div>
    <div class="contact-lines">
      <span class="contact-line"><svg class="contact-icon"><use href="#icon-phone"/></svg>020 7946 0321</span>
      <span class="contact-line"><svg class="contact-icon"><use href="#icon-web"/></svg>www.pinecrestdwellings.example</span>
    </div>
  </div>
  <svg class="accent-band" preserveAspectRatio="none" viewBox="0 0 400 24"><use href="#band"/></svg>
</section>

</body>
</html>
```